High-end construction company needs a business card design

We need a modern looking business card that draws people in, is memorable and looks so good people will want to sick it on their fridges.
On the first side what is needed are:
Logo
My name - Tomasz Brelwik
Title - Managing Director
Website - www.varkelt.co.uk
Email - tomasz@varkelt.co.uk
Telephone - 020 5194 6281
Mobile - 07845139072
On the back side was is needed is a list of all the services we provide:
-Kitchen Renovations
-Bathroom Renovations
-House Renovations
-Garage Conversions
-Extensions
-Loft Conversions
-Conservatories
-Carpentry
-Tiling
-Electrical
-Plumbing & Heating
-Bricklaying
-Landscaping
-Decorating
-Plastering
We would like the colours to be the same shades as on the logo with grey or black for the words.
Target Market(s)
Anyone who needs building work done
Contact Information for Business Card
This business card is for a construction company which strives to deliver excellent service and quality.
The look and feel of the card should represent this.
Requirements
Must have
- On the first side what is needed are:
Logo
My name - Tomasz Brelwik
Title - Managing Director
Website - www.varkelt.co.uk
Email - tomasz@varkelt.co.uk
Telephone - 020 5194 6281
Mobile - 07845139072
Nice to have
- Cool looking features

```html
<!DOCTYPE html>
<html lang="en">
<head>
<meta charset="utf-8">
<title>Varkelt Construction Ltd – Business Card</title>
<link rel="stylesheet" href="https://fonts.googleapis.com/css2?family=Montserrat:wght@700;800&family=Roboto:wght@400;500&display=swap">
<style>
  :root {
    --canvas: #e9eae8;
    --card: #2f3031;
    --card-edge: #262727;
    --green: #6cc644;
    --green-deep: #3f9a3a;
    --text-light: #f2f2f2;
  }
  * { box-sizing: border-box; margin: 0; padding: 0; }
  html, body { width: 1200px; height: 896px; overflow: hidden; }
  body {
    background: var(--canvas);
    font-family: "Roboto", Arial, sans-serif;
    display: flex;
    align-items: center;
    justify-content: center;
    gap: 40px;
  }
  .card {
    position: relative;
    width: 540px;
    height: 350px;
    background: linear-gradient(160deg, #38393a 0%, var(--card) 55%, var(--card-edge) 100%);
    border-radius: 4px;
    box-shadow: 0 12px 30px rgba(0,0,0,.28);
    overflow: hidden;
    color: var(--text-light);
  }

  /* brand name lockup */
  .brand {
    display: flex;
    align-items: center;
    gap: 12px;
  }
  .brand-mark {
    width: 26px;
    height: 26px;
    background: var(--green);
    flex: none;
  }
  .brand-name {
    font-family: "Montserrat", Arial, sans-serif;
    font-weight: 800;
    color: var(--green);
    font-size: 30px;
    line-height: 1.02;
    letter-spacing: .5px;
    text-transform: uppercase;
    white-space: nowrap;
  }
  .brand-name small { display: block; font-size: inherit; font-weight: 800; }

  /* services side */
  .card-services { padding: 44px 36px 0; }
  .card-services .brand { justify-content: center; }
  .services-heading {
    display: flex;
    align-items: center;
    gap: 14px;
    margin: 26px 0 18px;
    font-family: "Montserrat", Arial, sans-serif;
    font-weight: 700;
    font-size: 18px;
    letter-spacing: 1px;
    color: var(--green);
  }
  .services-heading::before,
  .services-heading::after {
    content: "";
    flex: 1;
    height: 1.5px;
    background: var(--green-deep);
  }
  .services-list {
    list-style: none;
    text-align: center;
    font-size: 13.5px;
    line-height: 1.75;
  }
  .services-list li { display: inline-block; white-space: nowrap; }
  .services-list li::before {
    content: "";
    display: inline-block;
    width: 5px; height: 5px;
    border-radius: 50%;
    background: var(--green);
    margin: 0 6px 2px 8px;
    vertical-align: middle;
  }

  /* contact side */
  .card-contact {
    display: flex;
    align-items: center;
    padding: 0 28px 18px 28px;
  }
  .card-contact .brand { width: 226px; flex: none; }
  .card-contact .brand-name { font-size: 20px; }
  .divider {
    width: 1.5px;
    flex: none;
    align-self: stretch;
    margin: 48px 22px 62px 18px;
    background: var(--green-deep);
  }
  .contact { min-width: 0; }
  .contact-name {
    font-family: "Montserrat", Arial, sans-serif;
    font-weight: 800;
    font-size: 17px;
    color: var(--green);
    text-transform: uppercase;
    letter-spacing: .3px;
    white-space: nowrap;
  }
  .contact-role { font-size: 14px; margin: 2px 0 12px; }
  .contact-address { font-size: 14px; line-height: 1.4; font-style: normal; margin-bottom: 14px; }
  .contact-lines { list-style: none; font-size: 14px; line-height: 1.55; }
  .contact-lines li { display: flex; align-items: center; gap: 8px; white-space: nowrap; }
  .contact-lines svg { width: 12px; height: 12px; fill: var(--green); flex: none; }
  .edge-band {
    position: absolute;
    left: 0; right: 0; bottom: 0;
    height: 12px;
    display: flex;
  }
  .edge-band span:first-child { flex: 3; background: var(--green); }
  .edge-band span:last-child { flex: 1; background: var(--green-deep); }
</style>
</head>
<body>

<section class="card card-services" aria-label="Services side">
  <div class="brand">
    <span class="brand-mark"></span>
    <p class="brand-name">Varkelt<small>Construction Ltd</small></p>
  </div>
  <h2 class="services-heading">SERVICES</h2>
  <ul class="services-list">
    <li>Kitchen Renovations</li>
    <li>Bathroom Renovations</li>
    <li>House Renovations</li>
    <li>Garage Conversions</li>
    <li>Extensions</li>
    <li>Loft Conversions</li>
    <li>Conservatories</li>
    <li>Carpentry</li>
    <li>Tiling</li>
    <li>Electrical</li>
    <li>Plumbing &amp; Heating</li>
    <li>Bricklaying</li>
    <li>Landscaping</li>
    <li>Decorating</li>
    <li>Plastering</li>
  </ul>
</section>

<section class="card card-contact" aria-label="Contact side">
  <div class="brand">
    <span class="brand-mark"></span>
    <p class="brand-name">Varkelt<small>Construction</small><small>Ltd</small></p>
  </div>
  <div class="divider"></div>
  <div class="contact">
    <h1 class="contact-name">Tomasz Brelwik</h1>
    <p class="contact-role">Managing Director</p>
    <address class="contact-address">14-16 Harlow Mews<br>London, N4 2PL</address>
    <ul class="contact-lines">
      <li><svg viewBox="0 0 24 24"><path d="M6.6 10.8a15.1 15.1 0 0 0 6.6 6.6l2.2-2.2c.3-.3.7-.4 1-.2 1.1.4 2.3.6 3.6.6.6 0 1 .4 1 1V20c0 .6-.4 1-1 1A17 17 0 0 1 3 4c0-.6.4-1 1-1h3.5c.6 0 1 .4 1 1 0 1.3.2 2.5.6 3.6.1.3 0 .7-.2 1z"/></svg>020 5194 6281</li>
      <li><svg viewBox="0 0 24 24"><path d="M7 1h10a2 2 0 0 1 2 2v18a2 2 0 0 1-2 2H7a2 2 0 0 1-2-2V3a2 2 0 0 1 2-2zm0 3v14h10V4zm5 15.5a1.2 1.2 0 1 0 0 2.4 1.2 1.2 0 0 0 0-2.4z"/></svg>07845139072</li>
      <li><svg viewBox="0 0 24 24"><path d="M2 5h20v14H2zm2 2v.4l8 5 8-5V7zm0 2.8V17h16V9.8l-8 5z"/></svg>tomasz@varkelt.co.uk</li>
      <li><svg viewBox="0 0 24 24"><path d="M12 2a10 10 0 1 0 0 20 10 10 0 0 0 0-20zm6.9 6h-3a15.7 15.7 0 0 0-1.4-3.6A8 8 0 0 1 18.9 8zM12 4c.8 1.2 1.5 2.5 1.9 4h-3.8c.4-1.5 1.1-2.8 1.9-4zM4.3 14a8 8 0 0 1 0-4h3.4a16.5 16.5 0 0 0 0 4zm.8 2h3a15.7 15.7 0 0 0 1.4 3.6A8 8 0 0 1 5.1 16zm3-8h-3a8 8 0 0 1 4.4-3.6A15.7 15.7 0 0 0 8.1 8zM12 20c-.8-1.2-1.5-2.5-1.9-4h3.8c-.4 1.5-1.1 2.8-1.9 4zm2.3-6H9.7a14.7 14.7 0 0 1 0-4h4.6a14.7 14.7 0 0 1 0 4zm.2 5.6c.6-1.1 1.1-2.3 1.4-3.6h3a8 8 0 0 1-4.4 3.6zm1.8-5.6a16.5 16.5 0 0 0 0-4h3.4a8 8 0 0 1 0 4z"/></svg>www.varkelt.co.uk</li>
    </ul>
  </div>
  <div class="edge-band"><span></span><span></span></div>
</section>

</body>
</html>
```